Update our OBGYN business card look and info

We are an OBGYN office. Our logo is nice but would like to "woman" part of the logo to be a darker color, to contrast with the flower that surrounds it. Maybe make our practice name Bloom Harbor Health more feminine. Our practice caters to women only. All providers and staff are female.

Target Market(s)

Females 16-65.

Industry/Entity Type

Business

Contact Information for Business Card

See attached upload. The ONLY CHANGE to the information is DELETE the name Paula Renwick, Midwife and REPLACE with Dora Fintelli, Midwife

Logo Text

Bloom Harbor Health Obstetrics & Gynecology

Font styles to use
Serif
Script

Colors
85cae6
0692cd
33a6d7
85abd2
f59195
eea4c8
cadf82
fac994
d3a5cc

```html
<!DOCTYPE html>
<html lang="en">
<head>
<meta charset="utf-8">
<title>Bloom Harbor Health – Business Card</title>
<link rel="stylesheet" href="https://fonts.googleapis.com/css2?family=Tinos:wght@400;700&display=swap">
<style>
  :root {
    --page-bg: #dcd7d0;
    --blue-light: #3f93d4;
    --blue-mid: #1768b6;
    --blue-deep: #0a4f9c;
    --teal-line: #2f8aa8;
    --frost-top: #eceeef;
    --frost-bottom: #d9dcde;
    --text-light: #e6eef6;
    --brand-blue: #0b5a9a;
    --brand-navy: #0d3f78;
  }
  * { margin: 0; padding: 0; box-sizing: border-box; }
  html, body {
    width: 1200px; height: 970px; overflow: hidden;
    background: var(--page-bg);
  }
  .business-card {
    position: absolute; left: 70px; top: 185px;
    width: 1060px; height: 600px;
    border-radius: 20px; overflow: hidden;
    background: linear-gradient(180deg, var(--frost-top), var(--frost-bottom));
    box-shadow: 0 10px 30px rgba(0,0,0,0.18);
    font-family: "Tinos", "Times New Roman", serif;
  }
  .card-shapes { position: absolute; inset: 0; }
  .provider-list, .contact-list, .address {
    position: absolute; left: 46px; color: var(--text-light);
    font-size: 28px; line-height: 38px; list-style: none;
  }
  .provider-list { top: 74px; }
  .contact-list { top: 302px; line-height: 35px; }
  .contact-list li { display: flex; align-items: center; gap: 14px; }
  .contact-icon { width: 30px; height: 30px; flex: none; }
  .address { top: 446px; }
  .brand {
    position: absolute; left: 562px; top: 222px; width: 470px;
    display: flex; flex-direction: column; align-items: center;
  }
  .brand-lockup { display: flex; align-items: center; gap: 14px; }
  .brand-dot {
    width: 56px; height: 56px; border-radius: 50%;
    background: var(--brand-blue);
  }
  .brand-name {
    font-size: 40px; color: var(--brand-blue); font-weight: 400;
    white-space: nowrap;
  }
  .brand-specialty {
    margin-top: 28px; font-size: 23px; font-weight: 700;
    color: var(--brand-navy); letter-spacing: 0.3px; white-space: nowrap;
  }
</style>
</head>
<body>
  <div class="business-card">
    <svg class="card-shapes" width="1060" height="600" viewBox="0 0 1060 600">
      <defs>
        <linearGradient id="panelBlue" x1="0" y1="0" x2="1" y2="1">
          <stop offset="0" stop-color="var(--blue-light)"/>
          <stop offset="0.5" stop-color="var(--blue-mid)"/>
          <stop offset="1" stop-color="var(--blue-deep)"/>
        </linearGradient>
      </defs>
      <path d="M0 0 H562 Q470 300 562 600 H0 Z" fill="url(#panelBlue)"/>
      <path d="M572 0 Q482 300 572 600" fill="none" stroke="var(--teal-line)" stroke-width="3"/>
      <path d="M582 0 Q496 300 582 600" fill="none" stroke="var(--teal-line)" stroke-width="1.2" opacity="0.6"/>
    </svg>

    <ul class="provider-list">
      <li>Marian Oakes, MD</li>
      <li>Lena Whitcombe, MD</li>
      <li>Nadia Ferrow, MD</li>
      <li>Dora Fintelli, Midwife</li>
      <li>Celia Brandt, Midwife</li>
    </ul>

    <ul class="contact-list">
      <li>
        <svg class="contact-icon" viewBox="0 0 30 30" aria-hidden="true">
          <circle cx="15" cy="15" r="13" fill="none" stroke="#e6eef6" stroke-width="1.6"/>
          <rect x="11" y="7.5" width="8" height="15" rx="1.5" fill="none" stroke="#e6eef6" stroke-width="1.5"/>
          <circle cx="15" cy="19.5" r="0.9" fill="#e6eef6"/>
        </svg>
        <span>555-210-4830</span>
      </li>
      <li>
        <svg class="contact-icon" viewBox="0 0 30 30" aria-hidden="true">
          <circle cx="15" cy="15" r="13" fill="none" stroke="#e6eef6" stroke-width="1.6"/>
          <rect x="8" y="12" width="14" height="8" rx="1.5" fill="#e6eef6"/>
          <rect x="10.5" y="8" width="9" height="4" fill="none" stroke="#e6eef6" stroke-width="1.3"/>
          <rect x="10.5" y="18" width="9" height="4" fill="#1768b6" stroke="#e6eef6" stroke-width="1.2"/>
        </svg>
        <span>555-210-4871</span>
      </li>
      <li>
        <svg class="contact-icon" viewBox="0 0 30 30" aria-hidden="true">
          <circle cx="15" cy="15" r="13" fill="none" stroke="#e6eef6" stroke-width="1.6"/>
          <circle cx="15" cy="15" r="8" fill="none" stroke="#e6eef6" stroke-width="1.3"/>
          <ellipse cx="15" cy="15" rx="3.5" ry="8" fill="none" stroke="#e6eef6" stroke-width="1.1"/>
          <line x1="7" y1="15" x2="23" y2="15" stroke="#e6eef6" stroke-width="1.1"/>
        </svg>
        <span>www.bloomharborhealth.com</span>
      </li>
    </ul>

    <p class="address">418 Linden Ave, Ste 3B<br>Fairhaven, GA 30999-0142</p>

    <div class="brand">
      <div class="brand-lockup">
        <span class="brand-dot" aria-hidden="true"></span>
        <span class="brand-name">Bloom Harbor Health</span>
      </div>
      <div class="brand-specialty">OBSTETRICS &amp; GYNECOLOGY</div>
    </div>
  </div>
</body>
</html>
```